Design a "healthy, happy dog and cat" cheque/check background

I am looking for a few design concepts featuring a happy healthy dog and cat, that will be used as the background of a paper cheque/check.

This will require Photoshop and stock photos.

Here is the design brief: https://docs.plinvaro.com/document/d/4Rt8mKx2LqW9zVbN3cHy7TfJ1sDp6GaE0uYoZiXeMwnB/edit?usp=sharing

Colors

Designer to choose colors to be used in the design.

Requirements
Must have
• A happy dog and cat the main focus within the "empty" central part of the cheque/check, and a complementary background for the rest of the cheque, following the design guidelines in the attached plinvaro doc.

```html
<!DOCTYPE html>
<html lang="en">
<head>
<meta charset="utf-8">
<title>Personal Cheque – Cat Design</title>
<link rel="stylesheet" href="https://fonts.googleapis.com/css2?family=Arimo:wght@400;700&family=Share+Tech+Mono&display=swap">
<style>
  :root {
    --page: #ffffff;
    --ink: #2f2f2f;
    --ink-strong: #000000;
    --rule: #4a4a4a;
    --field: #ffffff;
    --bg-left: #a9a27c;
    --bg-left-light: #c2b990;
    --bg-center: #c99562;
    --bg-center-light: #dcb48a;
    --bg-right: #8c8a68;
    --badge: #c4b69a;
    --mark: #3a3a3a;
  }
  * { margin: 0; padding: 0; box-sizing: border-box; }
  html, body { width: 1200px; height: 544px; overflow: hidden; background: var(--page); }
  body { position: relative; font-family: "Arimo", Arial, sans-serif; color: var(--ink); }

  .cheque { position: absolute; left: 24px; top: 20px; width: 1170px; height: 388px; overflow: hidden; }
  .cheque-photo {
    position: absolute; inset: 0;
    background:
      radial-gradient(ellipse 280px 330px at 600px 230px, var(--bg-center-light) 0%, var(--bg-center) 55%, rgba(201,149,98,0) 100%),
      linear-gradient(90deg, var(--bg-left-light) 0%, var(--bg-left) 40%, #b59670 55%, var(--bg-right) 85%, #9a8a6a 100%);
  }
  .abs { position: absolute; white-space: nowrap; }

  .drawer-name { left: 34px; top: 40px; font-size: 23px; font-weight: 700; color: var(--ink); }
  .drawer-address { left: 34px; top: 66px; font-size: 18.5px; line-height: 22px; color: var(--ink); }
  .cheque-number { left: 998px; top: 36px; font-size: 24px; font-weight: 700; color: var(--ink-strong); }

  .date-label { left: 760px; top: 89px; font-size: 20px; }
  .date-boxes { left: 824px; top: 70px; display: flex; gap: 4px; }
  .date-box { width: 36px; height: 36px; background: var(--field); }
  .date-format { left: 824px; top: 112px; display: flex; gap: 4px; }
  .date-format span { width: 36px; text-align: center; font-size: 13px; }

  .payee-label { left: 32px; top: 170px; font-size: 14px; line-height: 15px; }
  .amount-sign { left: 922px; top: 164px; font-size: 32px; }
  .amount-box { left: 949px; top: 154px; width: 193px; height: 48px; background: var(--field); }
  .amount-words { left: 894px; top: 235px; font-size: 15px; }

  .institution-mark { left: 40px; top: 272px; width: 52px; height: 52px; border-radius: 50%; background: var(--mark); }
  .institution { left: 129px; top: 280px; font-size: 18.5px; line-height: 20px; }
  .institution-name { font-weight: 700; font-size: 19px; }
  .company-name { left: 785px; top: 313px; font-size: 14.5px; }
  .memo-label { left: 37px; top: 362px; font-size: 12px; }

  .security-badge { left: 1136px; top: 252px; width: 30px; height: 134px; background: var(--badge); border: 1px solid #8a8070; }

  .rules { position: absolute; inset: 0; }

  .micr-line { position: absolute; left: 54px; top: 446px; font-family: "Share Tech Mono", monospace; font-size: 30px; letter-spacing: 2px; color: var(--ink-strong); white-space: nowrap; }
</style>
</head>
<body>
  <section class="cheque">
    <div class="cheque-photo" role="img" aria-label="Photograph of a contented orange tabby cat resting, set against a soft blurred green garden background"></div>

    <svg class="rules" width="1170" height="388" viewBox="0 0 1170 388">
      <g stroke="var(--rule)" stroke-width="1.2" fill="none">
        <line x1="32" y1="201" x2="898" y2="201"/>
        <line x1="898" y1="170" x2="898" y2="201"/>
        <line x1="34" y1="256" x2="881" y2="256"/>
        <line x1="881" y1="256" x2="888" y2="220"/>
        <line x1="34" y1="377" x2="562" y2="377"/>
        <line x1="662" y1="377" x2="1074" y2="377"/>
      </g>
    </svg>

    <div class="abs drawer-name">QLPS - Quickleaf Cheques Personal Cheque</div>
    <div class="abs drawer-address">15 Residential Street<br>Toronto, Ontario M1M 1M1</div>
    <div class="abs cheque-number">101</div>

    <div class="abs date-label">DATE</div>
    <div class="abs date-boxes">
      <span class="date-box"></span><span class="date-box"></span><span class="date-box"></span><span class="date-box"></span>
      <span class="date-box"></span><span class="date-box"></span><span class="date-box"></span><span class="date-box"></span>
    </div>
    <div class="abs date-format">
      <span>D</span><span>D</span><span>M</span><span>M</span><span>Y</span><span>Y</span><span>Y</span><span>Y</span>
    </div>

    <div class="abs payee-label">PAY TO THE<br>ORDER OF</div>
    <div class="abs amount-sign">$</div>
    <div class="abs amount-box"></div>
    <div class="abs amount-words">100 DOLLARS</div>

    <div class="abs institution-mark"></div>
    <div class="abs institution">
      <div class="institution-name">Your Financial Institution</div>
      <div>200 Finance Avenue</div>
      <div>Your City, Your Province A1B 2CS</div>
    </div>

    <div class="abs company-name">Optional Company Name</div>
    <div class="abs memo-label">MEMO</div>
    <div class="abs security-badge"></div>
  </section>

  <div class="micr-line">⑈101⑈ ⑆12345⑉678⑆ 12345⑉6789⑈</div>
</body>
</html>
```